Business Card Design

I need business cards designed for a new company i have started that makes cakes, particularly themed kids cakes with a really modern design and I would like to have my business cards reflect this. I have attached some photos of cakes I have made and would like some to be used.

Industry/Entity Type

Business

Contact Information for Business Card

Business Name: Tarts and Treats by Maren
Mobile: 0492 815 063
email: maren@tartsandtreatsbymaren.example.au
Instagram: instagram.com/tartsandtreatsbymaren/
Facebook: fb.me/tartsandtreatsbymaren

Colors
e667a6
b768aa
3276b5

Requirements
Must have
• Business Name: Tarts and Treats by Maren
• Mobile: 0492 815 063
• email: maren@tartsandtreatsbymaren.example.au
• Instagram: instagram.com/tartsandtreatsbymaren/
• Facebook: fb.me/tartsandtreatsbymaren
Nice to have
• 2 to 3 pictures of my cakes

```html
<!DOCTYPE html>
<html lang="en">
<head>
<meta charset="utf-8">
<title>Tarts and Treats by Maren – Business Card</title>
<link rel="stylesheet" href="https://fonts.googleapis.com/css2?family=Open+Sans:wght@400;600;700&display=swap">
<style>
  :root {
    --bg: #e9e4df;
    --purple: #b768aa;
    --purple-light: #c27bb6;
    --pink: #e667a6;
    --pink-light: #ec7fb6;
    --blue: #3276b5;
    --white: #ffffff;
    --dot: #e02a3a;
    --shadow: rgba(60, 40, 30, 0.25);
  }
  * { margin: 0; padding: 0; box-sizing: border-box; }
  html, body {
    width: 1200px; height: 950px; overflow: hidden;
    background: var(--bg);
    font-family: "Open Sans", Arial, sans-serif;
  }
  .canvas { position: relative; width: 1200px; height: 950px; }

  .card {
    position: absolute;
    width: 760px; height: 430px;
    overflow: hidden;
    box-shadow: 0 14px 30px var(--shadow);
  }

  /* Front */
  .card--front {
    left: 80px; top: 40px;
    background: linear-gradient(135deg, var(--purple-light), var(--purple));
    display: flex; align-items: center; justify-content: center;
  }
  .brand { display: flex; align-items: center; gap: 18px; }
  .brand__dot { width: 22px; height: 22px; border-radius: 50%; flex: none; }
  .brand__name { font-weight: 400; line-height: 1.05; text-align: center; }
  .brand__main { display: block; font-size: 58px; letter-spacing: -0.5px; }
  .brand__sub { display: block; font-size: 22px; letter-spacing: 6px; text-transform: uppercase; margin-top: 8px; }

  .card--front .brand__name { color: var(--white); }
  .card--front .brand__dot { background: var(--white); }

  /* Back */
  .card--back { left: 360px; top: 480px; background: var(--white); }
  .card__wave { position: absolute; inset: 0; width: 100%; height: 100%; }

  .contact {
    position: absolute; right: 34px; top: 30px;
    color: var(--white); text-align: right;
  }
  .contact__name { font-size: 24px; font-weight: 700; letter-spacing: 0.5px; text-transform: uppercase; }
  .contact__role { font-size: 15px; margin: 2px 26px 14px 0; }
  .contact__list { list-style: none; }
  .contact__item {
    display: flex; align-items: center; justify-content: flex-end; gap: 10px;
    font-size: 15px; line-height: 26px;
  }
  .contact__icon { width: 15px; height: 15px; flex: none; }
  .contact__square { width: 13px; height: 13px; background: var(--white); border-radius: 2px; flex: none; margin: 0 1px; }

  .card--back .brand { position: absolute; left: 110px; top: 268px; }
  .card--back .brand__main { font-size: 46px; }
  .card--back .brand__sub { font-size: 18px; letter-spacing: 5px; }
  .card--back .brand__name { color: var(--pink); }
  .card--back .brand__dot { background: var(--dot); width: 16px; height: 16px; }
</style>
</head>
<body>
<main class="canvas">

  <section class="card card--front" aria-label="Card front">
    <div class="brand">
      <span class="brand__dot"></span>
      <p class="brand__name">
        <span class="brand__main">Tarts and Treats</span>
        <span class="brand__sub">by Maren</span>
      </p>
    </div>
  </section>

  <section class="card card--back" aria-label="Card back">
    <svg class="card__wave" viewBox="0 0 760 430" preserveAspectRatio="none" aria-hidden="true">
      <defs>
        <linearGradient id="pinkBand" x1="0" y1="0" x2="1" y2="1">
          <stop offset="0" stop-color="#ec7fb6"/>
          <stop offset="1" stop-color="#e667a6"/>
        </linearGradient>
      </defs>
      <path d="M0 0 H760 V262 C640 222 500 200 360 196 C220 192 90 170 0 118 Z" fill="url(#pinkBand)"/>
      <path d="M0 124 C90 176 220 198 360 202 C500 206 640 228 760 270" fill="none" stroke="#3276b5" stroke-width="7"/>
    </svg>

    <div class="contact">
      <p class="contact__name">Dana Whitlock</p>
      <p class="contact__role">CEO/Founder</p>
      <ul class="contact__list">
        <li class="contact__item">0492 815 063
          <svg class="contact__icon" viewBox="0 0 16 16" aria-hidden="true"><rect x="4" y="1" width="8" height="14" rx="1.5" fill="none" stroke="#fff" stroke-width="1.6"/><circle cx="8" cy="12.5" r="0.9" fill="#fff"/></svg>
        </li>
        <li class="contact__item">maren@tartsandtreatsbymaren.example.au
          <svg class="contact__icon" viewBox="0 0 16 16" aria-hidden="true"><rect x="1" y="3" width="14" height="10" fill="#fff"/><path d="M1.5 3.5 L8 9 L14.5 3.5" fill="none" stroke="#e667a6" stroke-width="1.4"/></svg>
        </li>
        <li class="contact__item">tartsandtreatsbymaren <span class="contact__square"></span></li>
        <li class="contact__item">tartsandtreatsbymaren <span class="contact__square"></span></li>
      </ul>
    </div>

    <div class="brand">
      <span class="brand__dot"></span>
      <p class="brand__name">
        <span class="brand__main">Tarts and Treats</span>
        <span class="brand__sub">by Maren</span>
      </p>
    </div>
  </section>

</main>
</body>
</html>
```